Business card design for holistic health care clinic

We need a double-sided business card design for our holistic health care clinic that integrates our logo design and also its color scheme. My business is called Valmira. It is an integrative medicine clinic. You have already done the logo for me. Please ensure an elegant and upscale design that is not cluttered, but still has all the necessary information (please see below for details).

Target Market(s)

Wellness, fitness, rehabilitation for educated, well-traveled open-minded clients who are focused on natural, organic, balanced and preventive healthcare and lifestyle.

Industry/Entity Type

Medical

Contact Information for Business Card

Modern, clean.

Number of Pages Required

1 page

Font styles to use
Serif
Sans Serif

Colors

Designer to choose colors to be used in the design.

Requirements
Must have
• Logo on one side, all other information on the other side.
• Other information should include:
• Tobias Wrenfeld - DOE, CPT, LMT
• 4100 East Marrow Drive
• Austin, TX 78119
• 512 555 0148
• 818 555 0192
• info@ValmiraHealth.example
• t.wrenfeld@ValmiraHealth.example
Nice to have
• Darker background on front - but not totally black - shaded/dark gray.

```html
<!DOCTYPE html>
<html lang="en">
<head>
<meta charset="utf-8">
<title>Valmira – Business Card</title>
<link rel="stylesheet" href="https://fonts.googleapis.com/css2?family=Nunito:wght@700;800&family=Roboto:ital,wght@0,400;0,700;1,400&family=Roboto+Condensed:wght@700&display=swap">
<style>
  :root {
    --page-bg: #e2e2e2;
    --card-dark: #282828;
    --brand-blue: #1690d0;
    --band-blue: #0a8ccb;
    --card-light: #f3f3f3;
    --ink-dark: #262626;
    --ink-white: #ffffff;
    --ink-grey: #4a4a4a;
    --rule-grey: #6a6a6a;
  }
  * { margin: 0; padding: 0; box-sizing: border-box; }
  html, body { width: 1200px; height: 960px; overflow: hidden; }
  body {
    background: var(--page-bg);
    position: relative;
    font-family: "Roboto", Arial, sans-serif;
  }
  .card {
    position: absolute;
    width: 600px;
    height: 343px;
    overflow: hidden;
  }
  .card--front { left: 314px; top: 113px; background: var(--card-dark); }
  .card--back  { left: 311px; top: 472px; background: var(--card-light); }

  .brand {
    position: absolute;
    left: 0; right: 0;
    text-align: center;
    color: var(--brand-blue);
    font-family: "Nunito", Arial, sans-serif;
  }
  .brand__name {
    display: block;
    font-weight: 800;
    font-size: 62px;
    line-height: 1;
    letter-spacing: 1px;
  }
  .brand__descriptor {
    display: block;
    font-weight: 700;
    font-size: 17px;
    margin-top: 6px;
  }
  .card--front .brand { top: 96px; }
  .card--back .brand  { top: 140px; }

  .contact-band {
    position: absolute;
    left: 0; bottom: 0;
    width: 100%;
    height: 124px;
    background: var(--band-blue);
  }
  .contact-list {
    position: absolute;
    left: 33px; top: 25px;
    list-style: none;
    color: var(--ink-white);
    font-size: 14.5px;
  }
  .contact-list li {
    display: flex;
    align-items: center;
    height: 19px;
  }
  .contact-list svg {
    width: 12px; height: 12px;
    margin-right: 10px;
    fill: var(--ink-dark);
  }
  .person {
    position: absolute;
    right: 36px; top: 26px;
    text-align: right;
    color: var(--ink-white);
    font-size: 14.5px;
    line-height: 18px;
  }
  .person__name {
    font-family: "Roboto Condensed", Arial, sans-serif;
    font-weight: 700;
    font-size: 20px;
    line-height: 20px;
    color: var(--ink-dark);
  }
  .person__credentials {
    font-family: "Roboto Condensed", Arial, sans-serif;
    font-weight: 700;
    font-size: 11px;
    line-height: 14px;
    color: var(--ink-dark);
    margin-bottom: 4px;
  }
  .tagline {
    position: absolute;
    left: 0; right: 0;
    top: 284px;
    display: flex;
    justify-content: center;
    align-items: center;
    gap: 8px;
    font-style: italic;
    font-size: 16px;
    color: var(--ink-grey);
  }
  .tagline::before, .tagline::after {
    content: "";
    width: 105px;
    height: 1px;
    background: linear-gradient(to right, transparent, var(--rule-grey));
  }
  .tagline::after { background: linear-gradient(to left, transparent, var(--rule-grey)); }
</style>
</head>
<body>
  <section class="card card--front">
    <div class="brand">
      <span class="brand__name">VALMIRA</span>
      <span class="brand__descriptor">Integrative Holistic Medicine</span>
    </div>
    <div class="contact-band">
      <ul class="contact-list">
        <li><svg viewBox="0 0 12 12"><path d="M2.5 0.5 L4.5 0.5 L5.2 3.2 L3.8 4.3 Q5 7 7.7 8.2 L8.8 6.8 L11.5 7.5 L11.5 9.5 Q11.5 11.5 9.5 11.5 Q1 11 0.5 2.5 Q0.5 0.5 2.5 0.5Z"/></svg>512 555 0148</li>
        <li><svg viewBox="0 0 12 12"><path d="M3 0 H9 Q10 0 10 1 V11 Q10 12 9 12 H3 Q2 12 2 11 V1 Q2 0 3 0Z M3.3 1.5 V9 H8.7 V1.5Z M5.3 10 H6.7 V11 H5.3Z"/></svg>818 555 0192</li>
        <li><svg viewBox="0 0 12 12"><path d="M0.5 2.5 H11.5 V9.5 H0.5Z M1.2 3 L6 6.6 L10.8 3 L10.8 3.8 L6 7.4 L1.2 3.8Z" fill-rule="evenodd"/></svg>t.wrenfeld@ValmiraHealth.example</li>
        <li><svg viewBox="0 0 12 12"><circle cx="6" cy="6" r="5.5"/></svg>www.ValmiraHealth.example</li>
      </ul>
      <div class="person">
        <div class="person__name">TOBIAS WRENFELD</div>
        <div class="person__credentials">DOE, CPT, LMT</div>
        <div>4100 East Marrow Drive</div>
        <div>Austin, TX 78119</div>
      </div>
    </div>
  </section>

  <section class="card card--back">
    <div class="brand">
      <span class="brand__name">VALMIRA</span>
      <span class="brand__descriptor">Integrative Holistic Medicine</span>
    </div>
    <p class="tagline">helping the body help itself</p>
  </section>
</body>
</html>
```